Vorelan.com Personal Trainer/Fitness Website

I want a website to market my personal training/Outdoor Bootcamp Class services, as well as to ditribute nutrivex. I need a logo as well I included an address for the Harbor Gales 1975 logo. I'd like Vorelan in place of Harbor Gales, and in Black and white, just different enough so I can't get sued by the PBL.
https://www.pictofind.example/imgres?imgurl=http%3A%2F%2Fwww.darnell-quibury.example%2Fwp-content%2Fuploads%2F2014%2F01%2Fgales_logo4.jpg&imgrefurl=http%3A%2F%2Fwww.darnell-quibury.example%2Fpbl-logo-redesigns-harbor-gales%2F&docid=_qkwzR7TBAgXpL&tbnid=m4tpU8KdOXjnRP%3A&w=600&h=450&client=ms-android-carrier&bih=512&biw=360&ved=0ahUKEwiRtpgyp9HMAhUTwGMKHRPMBWMQMwg6KBQwFA&iact=mrc&uact=8.
It should be about 5 pages 1. home 2. about 3. Services 4. Blog/Videos and programs 5. Contact.
http://www.dorvinfitness.example.uk/ is a website I like the style of.

Target Market(s)

Seattle area

Industry/Entity Type

Fitness

Coding

Coded - Design and coding required

Number of Pages Required

4 page

Font styles to use
Serif
Sans Serif

Requirements
Must have
• A minimal look
Nice to have
• A logo similar to the 1975 Harbor Galewinds Logo, with a Small Milo Brandt ripping his shirt open(with a picture of the logo on his shirt, picture within picture) to turn into Ironjaw in the center. Skyline is black, Background and small figure white(with black logo on shirt)

```html
<!DOCTYPE html>
<html lang="en">
<head>
<meta charset="utf-8">
<title>Vorelan — Personal Training &amp; Fitness</title>
<link rel="stylesheet" href="https://fonts.googleapis.com/css2?family=Montserrat:wght@400;500;600;700&family=Open+Sans:wght@400;600;700&display=swap">
<style>
  :root {
    --green: #3d9a26;
    --green-dark: #2f7d1b;
    --ink: #222222;
    --text: #6f6f6f;
    --topbar: #2f2f2f;
    --light-band: #ececec;
    --footer: #1b1b1b;
    --footer-bottom: #121212;
    --footer-text: #9a9a9a;
    --white: #ffffff;
    --rule: #e2e2e2;
  }
  * { box-sizing: border-box; margin: 0; padding: 0; }
  html, body { width: 1200px; height: 2493px; overflow: hidden; }
  body { font-family: "Open Sans", Arial, sans-serif; color: var(--text); background: var(--white); position: relative; }
  .heading { font-family: "Montserrat", Arial, sans-serif; }
  section, header, footer { position: absolute; left: 0; width: 1200px; }

  /* top bar */
  .topbar { top: 0; height: 48px; background: var(--topbar); }
  .topbar-phone { position: absolute; left: 766px; top: 12px; display: flex; align-items: center; gap: 8px; color: #e9e9e9; font-size: 15px; }
  .topbar-search { position: absolute; left: 911px; top: 8px; width: 178px; height: 34px; background: #484848; color: #cfcfcf; font-size: 12px; padding: 9px 12px; }
  .topbar-search svg { position: absolute; right: 12px; top: 11px; }

  /* navigation */
  .nav { top: 48px; height: 82px; background: var(--white); border-bottom: 1px solid #eee; }
  .brand { position: absolute; left: 111px; top: 12px; width: 62px; text-align: center; }
  .brand-mark { display: block; width: 40px; height: 40px; margin: 0 auto 4px; border-radius: 50%; border: 4px solid var(--green); }
  .brand-name { font-family: "Montserrat", Arial, sans-serif; font-weight: 700; font-size: 13px; color: var(--ink); letter-spacing: .5px; }
  .menu { position: absolute; top: 34px; left: 0; width: 100%; list-style: none; }
  .menu li { position: absolute; transform: translateX(-50%); font-family: "Montserrat", Arial, sans-serif; font-size: 12.5px; font-weight: 500; color: var(--ink); letter-spacing: .3px; }
  .menu li.active { color: var(--green); }

  /* hero */
  .hero { top: 130px; height: 435px; background: linear-gradient(100deg, #3a3634 0%, #6b5d55 30%, #4a4543 55%, #2a2a2b 80%, #1f1f20 100%); text-align: center; color: var(--white); }
  .hero::after { content: ""; position: absolute; inset: 0; background: rgba(0,0,0,.25); }
  .hero-content { position: absolute; z-index: 1; left: 0; right: 0; top: 240px; }
  .hero-title { font-size: 32px; font-weight: 500; letter-spacing: .5px; }
  .hero-text { margin-top: 16px; font-size: 13px; font-weight: 600; line-height: 30px; }
  .hero-dots { position: absolute; z-index: 1; left: 571px; top: 401px; display: flex; gap: 8px; }
  .hero-dots span { width: 10px; height: 10px; border-radius: 50%; background: rgba(255,255,255,.45); }
  .hero-dots span.on { background: var(--white); }

  /* welcome */
  .welcome { top: 565px; height: 555px; text-align: center; }
  .section-title { font-size: 26px; font-weight: 500; color: var(--ink); letter-spacing: .5px; }
  .welcome .section-title { margin-top: 55px; }
  .welcome-intro { margin: 22px auto 0; width: 1000px; font-size: 12px; line-height: 30px; }
  .features { position: absolute; top: 204px; left: 0; width: 100%; }
  .feature { position: absolute; width: 320px; transform: translateX(-50%); }
  .feature-icon { width: 113px; height: 113px; margin: 0 auto; border-radius: 50%; border: 2px solid #333; padding: 4px; }
  .feature-icon span { display: flex; align-items: center; justify-content: center; width: 100%; height: 100%; border-radius: 50%; background: #2c2c2c; }
  .feature.is-active .feature-icon { border-color: var(--green); }
  .feature.is-active .feature-icon span { background: var(--green); }
  .feature-title { margin-top: 22px; font-size: 15px; font-weight: 500; color: var(--ink); }
  .feature.is-active .feature-title, .feature.is-active .feature-link { color: var(--green); }
  .feature-text { margin-top: 10px; font-size: 11.5px; line-height: 30.5px; }
  .feature-link { margin-top: 8px; font-family: "Montserrat", Arial, sans-serif; font-size: 12px; font-weight: 700; color: var(--ink); }

  /* subscribe */
  .subscribe { top: 1120px; height: 366px; text-align: center; color: var(--white); background: linear-gradient(90deg, #5c5148 0%, #7a6a5e 20%, #4d4a48 45%, #6b5f57 70%, #3a3533 100%); }
  .subscribe::after { content: ""; position: absolute; inset: 0; background: rgba(0,0,0,.45); }
  .subscribe-inner { position: absolute; z-index: 1; left: 0; right: 0; top: 96px; }
  .subscribe .section-title { color: var(--white); }
  .subscribe-text { margin-top: 14px; font-size: 12.5px; line-height: 27px; font-weight: 600; }
  .subscribe-form { position: absolute; z-index: 1; top: 218px; left: 219px; display: flex; gap: 30px; }
  .field { width: 270px; height: 46px; border: 1px solid rgba(255,255,255,.85); border-radius: 2px; text-align: left; padding: 14px 18px; font-size: 12px; }
  .btn-subscribe { width: 169px; height: 46px; margin-left: -5px; background: var(--green); border-radius: 2px; font-family: "Montserrat", Arial, sans-serif; font-size: 15px; font-weight: 600; line-height: 46px; }

  /* services */
  .services { top: 1486px; height: 307px; background: var(--light-band); text-align: center; }
  .services .section-title { margin-top: 34px; }
  .service-tile { position: absolute; top: 91px; height: 146px; border: 3px solid var(--white); box-shadow: 0 2px 5px rgba(0,0,0,.25); }
  .tile-1 { left: 111px; width: 221px; background: linear-gradient(135deg, #f4e6b8 0%, #e4c86e 45%, #c9d9de 100%); }
  .tile-2 { left: 366px; width: 217px; background: linear-gradient(135deg, #5a5a5a 0%, #8a8a8a 50%, #3b3b3b 100%); }
  .tile-3 { left: 615px; width: 216px; background: linear-gradient(135deg, #55ad3a 0%, #3d9a26 100%); color: var(--white); font-size: 12px; line-height: 26px; padding-top: 28px; }
  .tile-4 { left: 866px; width: 221px; background: linear-gradient(135deg, #d9dde1 0%, #b6c5cf 45%, #4c97b8 100%); }
  .tile-arrow { margin: 10px auto 0; width: 20px; height: 20px; border-radius: 50%; background: var(--white); display: flex; align-items: center; justify-content: center; }

  /* transformations */
  .transformations { top: 1793px; height: 351px; }
  .transformations .section-title { text-align: center; margin-top: 51px; }
  .client { position: absolute; top: 113px; width: 476px; border-bottom: 1px solid var(--rule); height: 177px; }
  .client-left { left: 111px; }
  .client-right { left: 613px; }
  .client-photo { position: absolute; left: 2px; top: 0; width: 96px; height: 80px; border: 3px solid var(--white); box-shadow: 0 1px 4px rgba(0,0,0,.3); }
  .client-left .client-photo { background: linear-gradient(135deg, #7f9460, #4f6a3e 60%, #c8c0b0); }
  .client-right .client-photo { background: linear-gradient(135deg, #6b5a50, #3d3431 55%, #8b7b70); }
  .client-name { position: absolute; left: 118px; top: 20px; font-family: "Montserrat", Arial, sans-serif; font-size: 15px; color: var(--green); }
  .client-loc { position: absolute; left: 118px; top: 50px; font-size: 11px; color: #555; }
  .client-quote { position: absolute; left: 0; top: 96px; font-size: 12px; line-height: 27px; text-align: justify; }
  .client-quote::before { content: "\201C"; position: absolute; left: 0; top: -14px; font-family: Georgia, serif; font-size: 26px; color: #888; }
  .client-quote p { text-indent: 14px; }

  /* footer */
  .footer { top: 2144px; height: 266px; background: var(--footer); color: var(--footer-text); font-size: 11px; }
  .footer-col { position: absolute; top: 46px; }
  .footer-divider { position: absolute; top: 0; width: 1px; height: 266px; background: #2a2a2a; }
  .footer-title { font-family: "Montserrat", Arial, sans-serif; font-size: 15px; font-weight: 600; color: var(--white); margin-bottom: 18px; }
  .blog-item { display: flex; gap: 15px; margin-bottom: 30px; width: 320px; }
  .blog-thumb { flex: none; width: 83px; height: 53px; border: 2px solid var(--white); }
  .blog-thumb.b1 { background: linear-gradient(135deg, #e8d3b0, #b98e6b 50%, #6f8a4c); }
  .blog-thumb.b2 { background: linear-gradient(135deg, #7a5d48, #c4a084 50%, #4a3a30); }
  .blog-title { color: var(--white); font-size: 12px; font-weight: 600; line-height: 17px; }
  .blog-desc { font-size: 11px; line-height: 19px; }
  .contact-line { display: flex; gap: 12px; line-height: 20px; margin-bottom: 12px; }
  .contact-line svg { flex: none; margin-top: 3px; }
  .contact-name { color: var(--white); font-size: 12px; }
  .link-list { list-style: none; }
  .link-list li { line-height: 31.2px; font-size: 11px; color: #bbbbbb; }
  .footer-bottom { top: 2410px; height: 83px; background: var(--footer-bottom); color: #bbbbbb; font-size: 11px; }
  .copyright { position: absolute; left: 111px; top: 32px; }
  .social { position: absolute; left: 1015px; top: 30px; display: flex; gap: 7px; }
  .social span { width: 20px; height: 20px; border-radius: 50%; background: #2f74b5; }
</style>
</head>
<body>

<header class="topbar">
  <div class="topbar-phone">
    <svg width="18" height="18" viewBox="0 0 18 18" aria-hidden="true"><circle cx="9" cy="9" r="8" fill="none" stroke="#3d9a26" stroke-width="1.6"/><path d="M6 5.2l1.5-.4 1 2.2-.9.8c.5 1 1.3 1.8 2.3 2.3l.8-.9 2.2 1-.4 1.5c-3.3.2-6.8-3.3-6.5-6.5z" fill="#3d9a26"/></svg>
    (123) 456 789
  </div>
  <div class="topbar-search">Search..
    <svg width="12" height="12" viewBox="0 0 12 12" aria-hidden="true"><circle cx="5" cy="5" r="3.6" fill="none" stroke="#fff" stroke-width="1.6"/><path d="M7.7 7.7L11 11" stroke="#fff" stroke-width="1.8"/></svg>
  </div>
</header>

<header class="nav">
  <div class="brand">
    <span class="brand-mark"></span>
    <span class="brand-name">VORELAN</span>
  </div>
  <ul class="menu">
    <li class="active" style="left:534px">HOME</li>
    <li style="left:633px">ABOUT</li>
    <li style="left:744px">SERVICES</li>
    <li style="left:848px">BLOG</li>
    <li style="left:947px">VIDEOS</li>
    <li style="left:1059px">CONTACT</li>
  </ul>
</header>

<section class="hero" role="img" aria-label="Personal trainer working with a client lifting dumbbells in a gym">
  <div class="hero-content">
    <h1 class="hero-title heading">PERSONAL TRAINING SERVICES</h1>
    <p class="hero-text">Lorem ipsum dolor sit amet, consectetur adipiscing elit. Praesent imperdiet porta sem et imperdiet.<br>Praesent tristique nec enim at maximus. Duis non justo nunc</p>
  </div>
  <div class="hero-dots"><span></span><span class="on"></span><span></span></div>
</section>

<section class="welcome">
  <h2 class="section-title heading">WELCOME TO VORELAN</h2>
  <p class="welcome-intro">Quisque id odio sed metus lacinia sagittis at sed urna. Phasellus maximus velit justo, a euismod sapien dictum accumsan. Proin nec consequat quam, vel consequat leo.<br>Nunc quis finibus odio, vel convallis nunc. Proin malesuada placerat est, quis vehicula diam scelerisque non. Duis id dictum dui, non consectetur odio.</p>

  <div class="features">
    <div class="feature" style="left:266px">
      <div class="feature-icon"><span>
        <svg width="40" height="40" viewBox="0 0 40 40" aria-hidden="true"><rect x="5" y="5" width="30" height="30" fill="none" stroke="#fff" stroke-width="2.4"/><circle cx="24" cy="11" r="3" fill="#fff"/><path d="M11 22l6-6h6l3 5 4 1M20 16l-2 8 5 3v5M18 24l-5 4" fill="none" stroke="#fff" stroke-width="2.4" stroke-linecap="round"/></svg>
      </span></div>
      <h3 class="feature-title heading">TRAINING</h3>
      <p class="feature-text">Lorem ipsum dolor sit amet, consectetur adipiscing elit. Curabitur eu nisl rhoncus, ultrices neque a, condimentum mauris. Nunc a laoreet justo.</p>
      <p class="feature-link">» MORE DETAILS</p>
    </div>
    <div class="feature is-active" style="left:600px">
      <div class="feature-icon"><span>
        <svg width="40" height="40" viewBox="0 0 40 40" aria-hidden="true"><circle cx="20" cy="20" r="15" fill="none" stroke="#fff" stroke-width="2.2"/><path d="M13 26c1-6 3-10 7-12 2-1 4 0 4 2l-3 2c3 0 6 2 6 5 0 3-3 4-6 4h-7" fill="none" stroke="#fff" stroke-width="2.2" stroke-linejoin="round"/></svg>
      </span></div>
      <h3 class="feature-title heading">FITNESS</h3>
      <p class="feature-text">Nulla placerat, quam accumsan posuere auctor, quam quam pharetra risus, ac feugiat metus sapien nec leo. Duis iaculis, elit vel rhoncus volutpat.</p>
      <p class="feature-link">» MORE DETAILS</p>
    </div>
    <div class="feature" style="left:934px">
      <div class="feature-icon"><span>
        <svg width="40" height="40" viewBox="0 0 40 40" aria-hidden="true"><circle cx="20" cy="20" r="5" fill="#fff"/><g stroke="#fff" stroke-width="2.4" stroke-linecap="round"><path d="M20 6v5M20 29v5M6 20h5M29 20h5M10 10l3.5 3.5M26.5 26.5L30 30M30 10l-3.5 3.5M13.5 26.5L10 30"/></g></svg>
      </span></div>
      <h3 class="feature-title heading">OUTDOOR BOOTCAMP</h3>
      <p class="feature-text">Lorem ipsum dolor sit amet, consectetur adipiscing elit. Curabitur eu nisl rhoncus, ultrices neque a, condimentum mauris. Nunc a laoreet justo.</p>
      <p class="feature-link">» MORE DETAILS</p>
    </div>
  </div>
</section>

<section class="subscribe" role="img" aria-label="Group fitness class doing exercises on mats">
  <div class="subscribe-inner">
    <h2 class="section-title heading">SUBSCRIBE FOR UPDATES</h2>
    <p class="subscribe-text">Lorem ipsum dolor sit amet, consectetur adipiscing elit. Curabitur tortor lacus, blandit in hendrerit eget, convallis<br>vitae lacus. Ut nec ipsum eros. Praesent quis lacinia risus.</p>
  </div>
  <div class="subscribe-form">
    <div class="field">Name</div>
    <div class="field">Email Address</div>
    <div class="btn-subscribe">SUBSCRIBE</div>
  </div>
</section>

<section class="services">
  <h2 class="section-title heading">SERVICES</h2>
  <div class="service-tile tile-1" role="img" aria-label="Trainer coaching a senior client in a bright studio"></div>
  <div class="service-tile tile-2" role="img" aria-label="Athlete lifting a dumbbell on a bench"></div>
  <div class="service-tile tile-3" role="img" aria-label="Service highlight with green overlay">
    <p>Mauris sed nibh mattis, faucib<br>us nisl eu, varius quam.</p>
    <div class="tile-arrow"><svg width="10" height="10" viewBox="0 0 10 10" aria-hidden="true"><path d="M3.5 2l3 3-3 3" fill="none" stroke="#3d9a26" stroke-width="1.8"/></svg></div>
  </div>
  <div class="service-tile tile-4" role="img" aria-label="Group stretching class on blue mats"></div>
</section>

<section class="transformations">
  <h2 class="section-title heading">CLIENT TRANSFORMATIONS</h2>
  <article class="client client-left">
    <div class="client-photo" role="img" aria-label="Client portrait"></div>
    <p class="client-name">JOHN JOE</p>
    <p class="client-loc">LOCATION</p>
    <div class="client-quote"><p>Etiam non purus cursus libero faucibus posuere. Lorem ipsum dolor sit amet, consectetur adipiscing elit.</p></div>
  </article>
  <article class="client client-right">
    <div class="client-photo" role="img" aria-label="Client portrait"></div>
    <p class="client-name">EMMA JOE</p>
    <p class="client-loc">LOCATION</p>
    <div class="client-quote"><p>Duis iaculis, elit vel rhoncus volutpat, nulla leo rutrum felis, et pretium turpis nulla nec ex. Mauris quis porta purus. Aliquam lectus purus, porta a odio.</p></div>
  </article>
</section>

<footer class="footer">
  <div class="footer-divider" style="left:460px"></div>
  <div class="footer-divider" style="left:721px"></div>
  <div class="footer-divider" style="left:909px"></div>

  <div class="footer-col" style="left:111px">
    <h4 class="footer-title">OUR BLOG</h4>
    <div class="blog-item">
      <div class="blog-thumb b1" role="img" aria-label="Blog post photo"></div>
      <div><p class="blog-title">Lorem ipsum dolor sit amet onsectetu</p><p class="blog-desc">Nulla placerat, quam accumsan posuere auctor, quam quam pharetra risus</p></div>
    </div>
    <div class="blog-item">
      <div class="blog-thumb b2" role="img" aria-label="Blog post photo"></div>
      <div><p class="blog-title">Duis id dictum dui, non consectetur odio</p><p class="blog-desc">Feugiat metus sapien nec leo. Duis iaculis, elit vel rhoncus volutpat...</p></div>
    </div>
  </div>

  <div class="footer-col" style="left:502px">
    <h4 class="footer-title">CONTACT US</h4>
    <div class="contact-line">
      <svg width="10" height="14" viewBox="0 0 10 14" aria-hidden="true"><path d="M5 0a5 5 0 0 0-5 5c0 4 5 9 5 9s5-5 5-9a5 5 0 0 0-5-5z" fill="#3d9a26"/><circle cx="5" cy="5" r="1.8" fill="#1b1b1b"/></svg>
      <div><p class="contact-name">VORELAN</p><p>123, Lorem Ipsm, Lorem Ipsm<br>Lorem Ipsm - 123 000</p></div>
    </div>
    <div class="contact-line" style="margin-top:8px">
      <svg width="14" height="10" viewBox="0 0 14 10" aria-hidden="true"><rect width="14" height="10" rx="1" fill="#3d9a26"/><path d="M1 1l6 5 6-5" fill="none" stroke="#1b1b1b" stroke-width="1.2"/></svg>
      <p>info@vorelan.com</p>
    </div>
    <div class="contact-line" style="margin-top:16px">
      <svg width="14" height="14" viewBox="0 0 14 14" aria-hidden="true"><rect width="14" height="14" rx="2" fill="#3d9a26"/><path d="M4 3l1.4-.3.8 1.8-.8.7c.4.8 1 1.4 1.8 1.8l.7-.8 1.8.8L9.3 8.4C6.6 8.6 3.8 5.8 4 3z" fill="#1b1b1b"/></svg>
      <p>(800) 123 456 789</p>
    </div>
  </div>

  <div class="footer-col" style="left:760px">
    <h4 class="footer-title">INFORMATION</h4>
    <ul class="link-list"><li>About Us</li><li>Blog</li><li>Privacy Policy</li><li>Site Map</li><li>Contact Us</li></ul>
  </div>

  <div class="footer-col" style="left:956px">
    <h4 class="footer-title">QUICK LINKS</h4>
    <ul class="link-list"><li>Services</li><li>Locations</li><li>Send Mail</li><li>FAQ</li><li>News</li></ul>
  </div>
</footer>

<footer class="footer-bottom">
  <p class="copyright">Copyright@2016 vorelan. All Right Reserved.</p>
  <div class="social" aria-label="Social links"><span></span><span></span><span></span></div>
</footer>

</body>
</html>
```